Brochure 11 x 25.5 Trifold

Harbor Lane Associates, Inc. is a payroll, benefits, and HR administration company. We are in need of a brochure to showcase all of our services. Attached is a one-page information sheet that contains the information we want in the brochure as well as several images. The brochure is a 11 x 25.5 tri-fold (a sample is attached). Please use the colors in the attached logo and design to complement our website harborlanehq.com.
Target Market(s)
Company executives
Industry/Entity Type
Human Resource Management
Font styles to use
Other font styles liked:
- Avenir LT
Colors
Designer to choose colors to be used in the design.

```html
<!DOCTYPE html>
<html lang="en">
<head>
<meta charset="utf-8">
<title>Harbor Lane Associates – Trifold Brochure</title>
<link rel="stylesheet" href="https://fonts.googleapis.com/css2?family=Nunito+Sans:wght@400;600;700;800&display=swap">
<style>
:root{
  --navy:#0b3a5e;
  --navy-deep:#082c49;
  --green:#8cb03c;
  --orange:#e8742c;
  --red:#d9472b;
  --teal:#3fa7c9;
  --ink:#3d4650;
  --grey-bg:#a7a9ad;
  --paper:#ffffff;
  --photo-warm:#b9b2a8;
  --photo-cool:#8ea3b3;
}
*{box-sizing:border-box;margin:0;padding:0}
html,body{width:1200px;height:1153px;overflow:hidden;background:var(--grey-bg);font-family:"Nunito Sans",Arial,sans-serif;color:var(--ink)}
.sheet-label{position:absolute;left:54px;top:40px;font-size:10px;font-weight:700;color:#1b1b1b;letter-spacing:.2px}
.spread{position:absolute;left:56px;width:1073px;height:464px;background:var(--paper);overflow:hidden;box-shadow:0 4px 6px rgba(0,0,0,.28)}
.spread.outside{top:82px}
.spread.inside{top:630px}
.spread svg.art{position:absolute;left:0;top:0;width:1073px;height:464px}
.fold{position:absolute;top:0;width:24px;height:457px;pointer-events:none}
.fold.left{background:linear-gradient(90deg,rgba(0,0,0,0),rgba(0,0,0,.09))}
.fold.right{background:linear-gradient(90deg,rgba(0,0,0,.09),rgba(0,0,0,0))}
.abs{position:absolute}
.h-section{font-size:10.5px;font-weight:800;color:var(--navy);letter-spacing:.1px}
.rule{position:absolute;height:2px;width:64px;background:var(--green)}
.feature{position:absolute;left:15px;width:322px;display:flex;gap:10px;align-items:flex-start}
.feature .icon{width:34px;height:34px;flex:none;background:var(--navy);border-radius:4px;box-shadow:2px 2px 0 var(--green);display:flex;align-items:center;justify-content:center}
.feature p{font-size:8px;line-height:10px;text-align:justify;padding-top:2px}
.brand{display:flex;align-items:center;gap:7px;font-weight:700;color:var(--navy)}
.brand .dot{border-radius:50%;background:var(--green);flex:none}
.center{text-align:center}
.small{font-size:8px;line-height:10px}
.cta{position:absolute;background:var(--navy);color:#fff;border-radius:10px;font-size:10px;font-weight:700;display:flex;align-items:center;justify-content:center;gap:6px}
.tagline{color:#fff;font-size:19px;font-weight:700;line-height:23px}
.pill{position:absolute;background:var(--navy);color:#fff;border-radius:10px;font-size:8px;display:flex;align-items:center;justify-content:center;letter-spacing:.1px}
.stage h4{font-size:7.5px;font-weight:600;letter-spacing:.3px}
.stage p{font-size:5.6px;line-height:8px;color:#555;letter-spacing:.2px}
.svc{position:absolute}
.svc .head{display:flex;align-items:center;gap:5px;font-size:7.8px;font-weight:800;color:var(--navy);line-height:9px}
.svc .badge{width:17px;height:17px;border-radius:50%;background:var(--navy);border:1.5px solid #fff;box-shadow:0 0 0 1px var(--navy);flex:none}
.svc ul{margin:5px 0 0 10px;font-size:6.1px;line-height:7.8px;color:#333}
.svc ul li{margin-left:4px}
.tab{position:absolute;background:var(--navy);color:#fff;font-size:10px;font-weight:700;display:flex;align-items:center;padding-left:20px;border-radius:0 10px 10px 0}
.chart-title{position:absolute;font-size:6px;color:var(--navy)}
.body-copy{font-size:8px;line-height:10px;text-align:justify}
</style>
</head>
<body>

<div class="sheet-label">BROCHURE 11 X 25.5 TRIFOLD</div>

<!-- OUTSIDE SPREAD -->
<section class="spread outside">
  <svg class="art" viewBox="0 0 1073 464">
    <defs>
      <linearGradient id="teamPhoto" x1="0" y1="0" x2="1" y2="1">
        <stop offset="0" stop-color="#d9d6d0"/><stop offset=".5" stop-color="#a79e92"/><stop offset="1" stop-color="#5f6a72"/>
      </linearGradient>
      <linearGradient id="meetPhoto" x1="0" y1="0" x2="1" y2="0">
        <stop offset="0" stop-color="#e7e6e2"/><stop offset=".5" stop-color="#b9aea2"/><stop offset="1" stop-color="#cfd4d8"/>
      </linearGradient>
      <linearGradient id="duoPhoto" x1="0" y1="0" x2="1" y2="1">
        <stop offset="0" stop-color="#6b8598"/><stop offset=".5" stop-color="#a9b6c0"/><stop offset="1" stop-color="#7b95b0"/>
      </linearGradient>
    </defs>
    <!-- panel 1 photo -->
    <polygon points="0,0 425,0 330,166 0,166" fill="url(#teamPhoto)" role="img" aria-label="Photo: business team shaking hands in a bright office"/>
    <polygon points="420,0 448,0 345,166 320,166" fill="var(--navy)"/>
    <polyline points="448,0 350,166 0,166" fill="none" stroke="var(--green)" stroke-width="1.2" transform="translate(4,2)"/>
    <!-- panel 2 photo -->
    <polygon points="420,63 680,63 620,173 360,173" fill="none" stroke="var(--green)" stroke-width="1.5"/>
    <polygon points="428,58 688,58 628,166 368,166" fill="url(#meetPhoto)" role="img" aria-label="Photo: two colleagues meeting at a desk with a laptop"/>
    <polygon points="690,85 700,85 650,174 640,174" fill="var(--navy)"/>
    <!-- panel 3 photo -->
    <polygon points="880,0 1073,0 1073,320 780,313 735,300 735,260 860,40" fill="url(#duoPhoto)" role="img" aria-label="Photo: smiling colleagues working together at a laptop"/>
    <polygon points="835,0 880,0 790,160 770,150" fill="var(--navy)" opacity=".85"/>
    <polyline points="937,0 735,330" fill="none" stroke="var(--green)" stroke-width="1.2"/>
    <path d="M900 330 Q1030 345 1073 340" fill="none" stroke="var(--green)" stroke-width="1.2"/>
    <!-- navy & green wedges -->
    <polygon points="585,457 685,360 700,360 610,457" fill="var(--green)"/>
    <path d="M606 457 L730 310 Q740 300 760 311 L960 311 Q990 311 945 360 L870 457 Z" fill="var(--navy)"/>
    <path d="M730 310 Q760 290 800 311" fill="var(--navy)"/>
    <rect x="0" y="457" width="1073" height="7" fill="var(--green)"/>
  </svg>
  <div class="fold left" style="left:389px"></div>
  <div class="fold right" style="left:413px"></div>
  <div class="fold left" style="left:747px;opacity:.8"></div>

  <!-- panel 1 -->
  <h2 class="h-section abs" style="left:15px;top:182px">NOT JUST ANOTHER PAYROLL COMPANY</h2>
  <div class="rule" style="left:15px;top:198px"></div>
  <div class="feature" style="top:210px"><span class="icon"><svg width="18" height="14" viewBox="0 0 18 14"><circle cx="9" cy="4" r="2.5" fill="#fff"/><circle cx="3.5" cy="5" r="2" fill="#fff"/><circle cx="14.5" cy="5" r="2" fill="#fff"/><path d="M4 13c0-4 10-4 10 0z" fill="#fff"/></svg></span><p>Our team of experts is always a call or email away! Each of our customers receive a dedicated account representative that knows your specific service needs.</p></div>
  <div class="feature" style="top:251px"><span class="icon"><svg width="18" height="16" viewBox="0 0 18 16"><rect x="1" y="1" width="16" height="10" fill="none" stroke="#fff" stroke-width="1.4"/><polyline points="3,8 7,5 10,7 15,3" fill="none" stroke="#fff" stroke-width="1.2"/><path d="M9 11v4" stroke="#fff" stroke-width="1.4"/></svg></span><p>We are equipped with education, experience, certifications, and motivation. Our staff executes at the highest level in payroll and HR every day.</p></div>
  <div class="feature" style="top:292px"><span class="icon"><svg width="18" height="18" viewBox="0 0 18 18"><circle cx="9" cy="6" r="3" fill="#fff"/><circle cx="3" cy="14" r="2" fill="#fff"/><circle cx="15" cy="14" r="2" fill="#fff"/><path d="M9 9v3M9 12L3 14M9 12l6 2" stroke="#fff" stroke-width="1.2"/></svg></span><p>Employee information is automatically integrated across all modules, eliminating duplicate data entry and significantly reducing errors.</p></div>
  <div class="feature" style="top:333px"><span class="icon"><svg width="18" height="18" viewBox="0 0 18 18"><rect x="1" y="2" width="12" height="9" fill="none" stroke="#fff" stroke-width="1.4"/><rect x="13" y="5" width="4" height="12" fill="#fff"/><path d="M4 15h6" stroke="#fff" stroke-width="1.4"/></svg></span><p>Our advanced software is used to process payroll for over 88,000 companies and 2.2 million employees nation-wide. It makes even the most complex payrolls easy.</p></div>
  <div class="feature" style="top:374px"><span class="icon"><svg width="16" height="18" viewBox="0 0 16 18"><rect x="1" y="1" width="12" height="16" fill="none" stroke="#fff" stroke-width="1.4"/><path d="M4 6h6M4 9h6M4 12h4" stroke="#fff"/><path d="M15 3l-6 9" stroke="#fff" stroke-width="1.6"/></svg></span><p>Access employee information how you need it when you need it with our quick-access reports and intuitive report writer. We even provide custom reports!</p></div>
  <div class="feature" style="top:414px"><span class="icon"><svg width="20" height="14" viewBox="0 0 20 14"><path d="M5 13a4 4 0 010-8 5 5 0 019-1 4 4 0 011 9z" fill="#fff"/><rect x="8" y="7" width="4" height="4" fill="var(--navy)"/></svg></span><p>Our client branded, cloud-based Employee and Manager portals allow your employees to access their payroll information quicker and more securely than ever before!</p></div>

  <!-- panel 2 -->
  <div class="brand abs" style="left:440px;top:240px;font-size:16px"><span class="dot" style="width:20px;height:20px"></span>Harbor Lane Associates</div>
  <p class="small center abs" style="left:395px;top:287px;width:277px">From supporting the HR department to being the HR department, we provide tailored solutions based on the size and needs of your organization. We are here to make a difference beyond expectations.</p>
  <div class="cta" style="left:437px;top:335px;width:200px;height:19px">CALL US TODAY
    <svg width="10" height="10" viewBox="0 0 10 10"><circle cx="5" cy="5" r="4.3" fill="none" stroke="#fff"/><path d="M3.3 2.6l1 1-.5.8c.3.7.8 1.2 1.4 1.5l.8-.5 1 1-.6.9c-1.8-.3-3.2-1.7-3.6-3.6z" fill="#fff"/></svg>
    (225) 555-0148</div>
  <p class="small center abs" style="left:432px;top:371px;width:210px;font-weight:700;color:var(--navy)">info@harborlanehq.com<br>www.harborlanehq.com</p>
  <p class="small center abs" style="left:432px;top:401px;width:210px;color:#111">218 Quayside Drive<br>Harbor City, LA 70899</p>

  <!-- panel 3 -->
  <p class="tagline abs" style="left:733px;top:387px">An Essential Part<br>of Business</p>
  <div class="brand abs" style="left:922px;top:402px;font-size:10.5px"><span class="dot" style="width:13px;height:13px"></span>Harbor Lane Associates</div>
</section>

<!-- INSIDE SPREAD -->
<section class="spread inside">
  <svg class="art" viewBox="0 0 1073 464">
    <defs>
      <linearGradient id="groupPhoto" x1="0" y1="0" x2="1" y2="1">
        <stop offset="0" stop-color="#cfcac3"/><stop offset=".5" stop-color="#6f7a86"/><stop offset="1" stop-color="#b8c2cb"/>
      </linearGradient>
      <linearGradient id="reviewPhoto" x1="0" y1="0" x2="1" y2="0">
        <stop offset="0" stop-color="#3b4b5a"/><stop offset=".6" stop-color="#8a8f95"/><stop offset="1" stop-color="#5c6c7b"/>
      </linearGradient>
    </defs>
    <!-- panel 1 photo -->
    <polygon points="0,0 390,0 300,140 290,205 0,205" fill="url(#groupPhoto)" role="img" aria-label="Photo: professionals gathered around a laptop"/>
    <polygon points="365,0 395,0 325,120 290,122" fill="var(--navy)"/>
    <g role="img" aria-label="Laptop and phone showing the client portal dashboard">
      <rect x="167" y="164" width="153" height="94" rx="3" fill="#1d232a"/>
      <rect x="171" y="168" width="145" height="86" fill="#f2f4f6"/>
      <rect x="306" y="192" width="36" height="66" rx="4" fill="#1d232a"/>
      <rect x="309" y="198" width="30" height="54" fill="#e9ecef"/>
    </g>
    <!-- charts -->
    <g transform="translate(15,360)">
      <circle cx="52" cy="38" r="25" fill="var(--navy)"/>
      <path d="M52 38 L52 13 A25 25 0 0 0 31 24 Z" fill="var(--red)"/>
      <path d="M52 38 L31 24 A25 25 0 0 0 27 38 Z" fill="var(--green)"/>
    </g>
    <g transform="translate(146,370)" stroke="#ccc" stroke-width=".4">
      <line x1="12" y1="4" x2="140" y2="4"/><line x1="12" y1="17" x2="140" y2="17"/><line x1="12" y1="30" x2="140" y2="30"/><line x1="12" y1="43" x2="140" y2="43"/><line x1="12" y1="56" x2="140" y2="56"/>
      <polyline points="20,30 42,30 64,30 86,30 108,25 130,10" fill="none" stroke="#4a5bd6" stroke-width=".8"/>
      <polyline points="20,30 42,30 64,30 86,30 108,29 130,22" fill="none" stroke="var(--green)" stroke-width=".8"/>
      <polyline points="20,30 86,30 108,28 130,24" fill="none" stroke="var(--red)" stroke-width=".8"/>
    </g>
    <g transform="translate(265,360)">
      <circle cx="71" cy="38" r="24" fill="var(--navy)"/>
      <path d="M71 38 L71 14 A24 24 0 0 0 48 45 Z" fill="var(--green)"/>
    </g>
    <!-- lifecycle -->
    <g transform="translate(522,181)" fill="none" stroke-width="1.1">
      <path d="M-40 -28 A49 49 0 0 1 35 -34" stroke="#2a4a8a"/>
      <path d="M40 -26 A49 49 0 0 1 42 25" stroke="var(--orange)"/>
      <path d="M40 28 A49 49 0 0 1 -10 48" stroke="#8a8a3a"/>
      <path d="M-16 47 A49 49 0 0 1 -48 -8" stroke="var(--teal)"/>
      <path d="M-48 -14 A49 49 0 0 1 -42 -26" stroke="var(--red)"/>
      <path d="M0 -60 L0 -70" stroke="#e89a2c"/>
      <path d="M58 -20 L70 -30" stroke="#b8952a"/>
      <path d="M58 30 L72 38" stroke="#8dbdd4"/>
      <path d="M0 57 L0 67" stroke="var(--teal)"/>
      <path d="M-55 28 L-66 42" stroke="var(--navy)"/>
      <path d="M-58 -30 L-68 -38" stroke="var(--red)"/>
    </g>
    <!-- panel 3 photo -->
    <polygon points="890,314 1073,314 1073,457 720,457" fill="url(#reviewPhoto)" role="img" aria-label="Photo: two women reviewing documents at a laptop"/>
    <polygon points="760,440 810,370 830,370 780,457 760,457" fill="var(--navy)"/>
    <path d="M846 380 Q900 320 960 320 L1073 320" fill="none" stroke="var(--green)" stroke-width="1.2"/>
    <rect x="0" y="457" width="1073" height="7" fill="var(--green)"/>
  </svg>
  <div class="fold left" style="left:389px"></div>
  <div class="fold right" style="left:413px"></div>
  <div class="fold left" style="left:747px;opacity:.8"></div>

  <!-- panel 1 -->
  <h2 class="abs" style="left:15px;top:237px;font-size:11px;line-height:13px;font-weight:700;color:var(--navy)">Work less,<br>Accomplish more</h2>
  <div class="rule" style="left:15px;top:268px;width:135px;height:1.5px"></div>
  <p class="body-copy abs" style="left:15px;top:281px;width:321px">Harbor Lane Associates has been delivering quality HR and Payroll services for over 25 years. Our dedicated team of professionals is focused on being the best service provider in the industry. Our goal is to relieve business executives of the challenges of managing a dynamic and growing workforce in today’s regulatory environment and give them the freedom to focus on what drives their business.</p>
  <span class="chart-title" style="left:15px;top:350px">Total Compensation for Ellison</span>
  <span class="chart-title" style="left:146px;top:350px">Compensation History</span>
  <span class="chart-title" style="left:265px;top:350px">Retirement Details</span>
  <span class="abs" style="left:15px;top:365px;font-size:4px">Benefits</span>
  <span class="abs" style="left:15px;top:388px;font-size:4px">Retirement</span>
  <span class="abs" style="left:15px;top:410px;font-size:4px">Salary</span>
  <span class="abs" style="left:15px;top:434px;font-size:4px;line-height:5px">Benefits Compensation<br>2,035.28 (16.2%)</span>
  <span class="abs" style="left:265px;top:380px;font-size:4px">ER Match</span>
  <span class="abs" style="left:265px;top:424px;font-size:4px">FICA</span>

  <!-- panel 2 -->
  <div class="pill" style="left:403px;top:19px;width:263px;height:18px">FROM HIRE TO RETIRE, WE’VE GOT YOU COVERED</div>
  <div class="stage abs" style="left:503px;top:57px;width:90px"><h4 style="color:var(--orange)">HIRING</h4><p>Integrated cloud-based ATS, Auto post to job boards, applicant management and screening</p></div>
  <div class="stage abs" style="left:596px;top:122px;width:68px"><h4 style="color:#b38f2a">ONBOARDING</h4><p>Auto generate notice to new-hire, standard and customized forms and acknowledgements</p></div>
  <div class="stage abs" style="left:599px;top:205px;width:60px"><h4 style="color:#6fb3d1">PAYROLL</h4><p>HRIS, Direct deposits, New Hire Reporting, Employee Portal, Year End Reporting</p></div>
  <div class="stage abs" style="left:507px;top:262px;width:80px"><h4 style="color:var(--teal)">BENEFITS</h4><p>Online enrollment, application, benefit reconciliations, eligibility tracking notifications, retirement plan</p></div>
  <div class="stage abs" style="left:408px;top:219px;width:75px"><h4 style="color:var(--navy);line-height:8px">EMPLOYEE<br>MANAGEMENT</h4><p>Culture development, discipline, leave management, Workers’ Compensation claims, employee verifications, handbook</p></div>
  <div class="stage abs" style="left:405px;top:114px;width:55px"><h4 style="color:var(--red)">SEPARATION</h4><p>COBRA, Retirement plan assistance, DOL Notiring</p></div>
  <div class="abs center" style="left:490px;top:172px;width:64px;font-size:9px;line-height:9px;color:#555;letter-spacing:.3px">EMPLOYEE<br><b>LIFECYCLE</b></div>

  <div class="tab" style="left:357px;top:332px;width:112px;height:17px">OUR SERVICES</div>
  <div class="svc" style="left:377px;top:361px;width:145px"><div class="head"><span class="badge"></span>PAYROLL</div>
    <ul><li>Fast, efficient, accurate</li><li>Easy time file uploads or integrated time clock options</li><li>New hire reporting</li><li>Custom G/L file</li><li>Certified payroll option</li></ul></div>
  <div class="svc" style="left:534px;top:361px;width:150px"><div class="head"><span class="badge"></span>BENEFITS MANAGEMENT</div>
    <ul><li>Track new hire eligibility</li><li>Open enrollment assistance</li><li>Electronic enrollment</li><li>Remit retirement plan reports and funds</li><li>ACA compliance</li></ul></div>

  <!-- panel 3 -->
  <div class="svc" style="left:733px;top:19px;width:160px"><div class="head"><span class="badge"></span>PERFORMANCE MANAGEMENT</div>
    <ul><li>Custom job description</li><li>Custom tailored perform reviews</li><li>Corrective action notices</li></ul></div>
  <div class="svc" style="left:900px;top:19px;width:172px"><div class="head"><span class="badge"></span>HUMAN RESOURCE ADMINISTRATION</div>
    <ul><li>Wage and hour compliance</li><li>Employee handbooks</li><li>Employee discipline and termination consulting</li><li>Performance management</li><li>Unemployment administration</li></ul></div>
  <div class="svc" style="left:733px;top:91px;width:165px"><div class="head"><span class="badge"></span>EMPLOYEE ONBOARDING</div>
    <ul><li>Simple, accurate, paperless</li><li>Custom forms and acknowledgements</li><li>Standard forms (W-4, I-9, State withholding, etc)</li><li>Custom welcome videos</li></ul></div>
  <div class="svc" style="left:900px;top:91px;width:165px"><div class="head"><span class="badge"></span>TIME AND ATTENDANCE</div>
    <ul><li>Integrated with payroll (no double entry)</li><li>Mobile and geofencing options</li><li>Overtime notices</li><li>Online time-off requests</li><li>Biometric clocks</li><li>PTO tracking</li></ul></div>
  <div class="svc" style="left:733px;top:163px;width:160px"><div class="head"><span class="badge"></span>COBRA ADMINISTRATION</div>
    <ul><li>Initial notices</li><li>Open enrollment notices</li><li>Easy 24/7 online reporting</li><li>Online election and premium collection</li></ul></div>
  <div class="svc" style="left:900px;top:171px;width:125px"><div class="head"><span class="badge"></span>TALENT ACQUISITION</div>
    <ul><li>Custom careers page</li><li>Standard or custom job applications</li><li>Easy conversion of applicant data to employee data</li><li>Review, rate, and contact applicants</li><li>Easy posting to top job boards</li></ul></div>
  <div class="svc" style="left:733px;top:242px;width:150px"><div class="head"><span class="badge"></span>COMPLIANCE</div>
    <ul><li>Certified experts ensure compliance with all labor laws and regulations</li><li>OSHA Reporting</li><li>Affirmative Action (EEOC)</li><li>Family Medical Leave Act (FMLA)</li></ul></div>
  <div class="svc" style="left:900px;top:242px;width:140px"><div class="head"><span class="badge"></span>CAFETERIA/FSA/HRA<br>ADMINISTRATION</div>
    <ul><li>Plan documents/materials</li><li>Easy 24/7 online reporting</li><li>Claims processing</li><li>Plan testing</li></ul></div>
</section>

</body>
</html>
```